KBT Business Cards

We require business cards for our business. We would like a matte black back to the card, with our logo centred in the middle. The front side of the card is open to design.

Target Market(s)

Clients looking for legal services (professional)

Industry/Entity Type

Legal

Contact Information for Business Card

Doran Kelbrath
Partner
Mobile: 0461 738 524
Email: doran@kbtlaw.co
Website: www.kbtlaw.co
Level 3, 118 Wendmore Street
Sydney NSW 2000

Font styles to use
Other font styles liked:
• Avenir

Colors
f04a50
ffffff
1b1b1b

Requirements
Must have
• Black back with logo included in the centre of the card.
• Our font is Avenir.

```html
<!DOCTYPE html>
<html lang="en">
<head>
<meta charset="utf-8">
<title>KBT Business Cards</title>
<link href="https://fonts.googleapis.com/css2?family=Nunito+Sans:wght@400;600;800&display=swap" rel="stylesheet">
<style>
  :root {
    --brand-red: #f04a50;
    --brand-white: #ffffff;
    --brand-black: #1b1b1b;
    --card-deep: #0c0c0d;
    --card-sheen: #202022;
    --backdrop: #2a2a2d;
    --text-soft: #e6e6e6;
  }
  * { box-sizing: border-box; margin: 0; padding: 0; }
  html, body {
    width: 1200px;
    height: 800px;
    overflow: hidden;
    background: var(--backdrop);
    font-family: "Nunito Sans", "Avenir", sans-serif;
  }
  .canvas {
    position: relative;
    width: 1200px;
    height: 800px;
  }
  .card {
    position: absolute;
    top: 245px;
    width: 500px;
    height: 310px;
    border-radius: 4px;
    overflow: hidden;
    box-shadow: 0 18px 40px rgba(0,0,0,0.45);
  }
  .card--back { left: 70px; }
  .card--front { left: 630px; }
  .card__texture {
    position: absolute;
    inset: 0;
    background:
      linear-gradient(135deg, var(--card-sheen) 0%, var(--card-deep) 45%, var(--brand-black) 70%, var(--card-deep) 100%);
  }

  /* Back: centred brand name */
  .brand {
    position: absolute;
    inset: 0;
    display: flex;
    align-items: center;
    justify-content: center;
    gap: 14px;
  }
  .brand__mark {
    width: 22px;
    height: 22px;
    background: var(--brand-red);
  }
  .brand__name {
    color: var(--brand-white);
    font-weight: 800;
    font-size: 26px;
    letter-spacing: 2px;
    text-transform: uppercase;
  }

  /* Front: contact block */
  .contact {
    position: absolute;
    right: 34px;
    bottom: 62px;
    display: flex;
    align-items: center;
  }
  .person {
    text-align: right;
    padding-right: 16px;
  }
  .person__name {
    color: var(--brand-red);
    font-weight: 800;
    font-size: 19px;
    letter-spacing: 0.5px;
    text-transform: uppercase;
    line-height: 1.1;
  }
  .person__role {
    color: var(--text-soft);
    font-size: 12px;
    margin-top: 2px;
  }
  .divider {
    width: 1.5px;
    height: 58px;
    background: var(--brand-red);
  }
  .details {
    list-style: none;
    padding-left: 14px;
  }
  .details__item {
    display: flex;
    align-items: center;
    gap: 8px;
    color: var(--text-soft);
    font-size: 11.5px;
    line-height: 19px;
  }
  .details__icon {
    width: 11px;
    height: 11px;
    flex: none;
  }
  .address {
    position: absolute;
    right: 34px;
    bottom: 30px;
    color: var(--text-soft);
    font-size: 12px;
    letter-spacing: 0.2px;
  }
</style>
</head>
<body>
<main class="canvas">

  <section class="card card--back">
    <div class="card__texture" role="img" aria-label="Subtle dark geometric diamond texture"></div>
    <div class="brand">
      <span class="brand__mark"></span>
      <span class="brand__name">Kelbrath Bryce Legal</span>
    </div>
  </section>

  <section class="card card--front">
    <div class="card__texture" role="img" aria-label="Subtle dark geometric diamond texture"></div>

    <div class="contact">
      <div class="person">
        <p class="person__name">Doran Kelbrath</p>
        <p class="person__role">Partner</p>
      </div>
      <span class="divider"></span>
      <ul class="details">
        <li class="details__item">
          <svg class="details__icon" viewBox="0 0 12 12"><rect x="1.5" y="1.5" width="9" height="9" fill="none" stroke="#f04a50" stroke-width="1.4"/></svg>
          0461 738 524
        </li>
        <li class="details__item">
          <svg class="details__icon" viewBox="0 0 12 12"><rect x="0.5" y="2" width="11" height="8" fill="#f04a50"/><path d="M0.5 2 L6 6.5 L11.5 2" fill="none" stroke="#1b1b1b" stroke-width="1"/></svg>
          doran@kbtlaw.co
        </li>
        <li class="details__item">
          <svg class="details__icon" viewBox="0 0 12 12"><circle cx="6" cy="6" r="5.5" fill="#f04a50"/><path d="M0.5 6 H11.5 M6 0.5 V11.5" stroke="#1b1b1b" stroke-width="0.9"/><ellipse cx="6" cy="6" rx="2.4" ry="5.5" fill="none" stroke="#1b1b1b" stroke-width="0.9"/></svg>
          www.kbtlaw.co
        </li>
      </ul>
    </div>

    <p class="address">Level 3, 118 Wendmore Street, Sydney NSW 2000</p>
  </section>

</main>
</body>
</html>
```